Environmental Consultancey needs Web Design

A consultancey firm based in Papua New Guinea specialising servicing a client market primarily in Melanesia, the wider Pacific Region and South East Asia. The firm provides services to community development and resource extraction activites that incorporate sustainable livelihoods for local customary land owners with environmentally responsibile practices and a focus on maintaining biodiversity and ecosystem services. We aim to encompass Culture, Custom and Science in our approach. Our website preferentially will convey a relaxed Pacific Island feel in its colours and design rather than a sterile corporate feel. See attached logo that will need to be visible on page or which may provide basis for ideas for the page.

Target Market(s)

Our target market is primarily the oil, gas and mining industry, secondarily international donor and aid programs followed by government projects and not for profit programs. Services include:
1. Biodiversity and Conservation - Fauna and Flora survey, assessment, management, monitoring & research, protected areas & endangered & threatend species.
2. Social & Community - impact, stakeholder engagement, census and survey, land and community affairs, capacity building empowerment.
3. Environmental Management - sustainable use, enterprise development & management, biodiversity offsets.

Industry/Entity Type

Community

Requirements
Must have
• Multiple pages, Logo somewhere on home page. Space for a couple of photos that as yet ive not decieded upon.
Nice to have
• Perhaps incorporate shapes, texture and colours that convey a feel of the attached photo of a blue bird of paradise. The blue fine overlapping and interlocking feather patterns are appealing perhaps as a background and the other colours used in boarders ? Abstract is fine as would be symbolic images or tribal ambience. The company is all about blending humanity in all its forms with the environment.

```html
<!DOCTYPE html>
<html lang="en">
<head>
<meta charset="utf-8">
<title>Tidewater Habitats</title>
<link rel="stylesheet" href="https://fonts.googleapis.com/css2?family=Noto+Sans:wght@400;500&family=Didact+Gothic&family=Arimo&display=swap">
<style>
:root{
  --outer:#e6e6e6;
  --sky-1:#5ad4ee;
  --sky-2:#2bb6da;
  --page:#f4f6f3;
  --ink:#333333;
  --ink-soft:#555555;
  --teal-1:#6cc3bb;--teal-2:#82d4cc;--teal-3:#63bab2;--teal-4:#439c96;
  --olive-1:#8aa52f;--olive-2:#7f9b29;--olive-3:#6c8429;--olive-4:#7f992c;
  --slider-green:#5db47f;
  --slider-dark:#231f20;
  --chevron:#d8ea3a;
  --rule:#6b8a2a;
  --welcome:#1aa05a;
  --footer:#363636;
  --field:#232323;
  --submit:#37c4e6;
}
*{margin:0;padding:0;box-sizing:border-box}
html,body{width:1077px;height:1200px;overflow:hidden;background:var(--outer)}
body{font-family:"Noto Sans",Verdana,sans-serif;color:var(--ink);position:relative}
.abs{position:absolute}
.topbar{left:0;top:31px;width:1077px;height:58px;background:linear-gradient(180deg,var(--sky-1),var(--sky-2))}
.page{left:24px;top:89px;width:1029px;height:874px;
  background:radial-gradient(ellipse at 30% 85%,#dfe8dc 0%,transparent 55%),radial-gradient(ellipse at 75% 75%,#e4ebe2 0%,transparent 50%),linear-gradient(180deg,#ffffff 0%,var(--page) 30%,#eef2ec 100%)}
.brand{left:32px;top:29px;width:185px;height:187px;background:#fff;display:flex;flex-direction:column;align-items:center;justify-content:center;gap:10px}
.brand-dot{width:54px;height:54px;border-radius:50%;background:var(--sky-2)}
.brand-name{font-family:"Noto Sans",sans-serif;font-size:17px;color:#2a2a2a;text-align:center;line-height:1.2}
.search{left:597px;top:42px;width:227px;height:34px;background:#fff;display:flex;align-items:center;padding:0 10px 0 16px;justify-content:space-between}
.search span{font-family:Arimo,sans-serif;font-size:13px;color:#888}
.follow{left:865px;top:51px;font-size:11.5px;color:#333;font-family:Arimo,sans-serif}
.social{top:49px;width:21px;height:21px;background:#1c7fbf}
.nav{left:232px;top:106px;display:flex;width:786px}
.nav-item{width:98.25px;text-align:center}
.tile{height:77px;position:relative;display:flex;align-items:center;justify-content:center;padding-top:12px;border-radius:0 0 3px 3px}
.tile::before{content:"";position:absolute;left:0;top:0;right:0;height:12px;background:rgba(0,0,0,.22)}
.nav-label{font-family:Arimo,sans-serif;font-size:18px;margin-top:4px;display:block}
.hero{left:55px;top:243px;width:552px;height:373px;border:2px solid #1e2a2a;
  background:radial-gradient(ellipse at 45% 45%,#3a6fc0 0%,#2d5aa6 25%,transparent 50%),linear-gradient(160deg,#2e8f83 0%,#4aa39a 40%,#6fb7a6 70%,#cfd6b4 100%)}
.hero-caption{position:absolute;left:0;right:0;bottom:0;height:64px;background:rgba(40,45,45,.78);color:#fff;font-family:"Didact Gothic",sans-serif;font-size:26px;display:flex;align-items:center;padding-left:18px;white-space:nowrap}
.hero-shadow{left:170px;top:610px;width:730px;height:28px;background:radial-gradient(ellipse at center,rgba(0,0,0,.28),transparent 70%)}
.slides{left:608px;top:243px;width:416px;height:373px;background:var(--slider-green);padding:7px 4px 0 4px}
.slide{height:88px;display:flex;align-items:flex-start;color:#fff;padding:8px 10px 0 10px;border-bottom:2px dotted rgba(30,90,50,.55);margin:0 8px 0 0}
.slide.active{background:var(--slider-dark);height:81px;border-bottom:none;margin:0 0 6px 0}
.slide svg{flex:none;margin:22px 16px 0 4px}
.slide h3{font-weight:400;font-size:23px;line-height:1.2;margin-bottom:4px}
.slide p{font-size:12.5px;line-height:1.2}
.slide:last-child{border-bottom:none}
.rule{left:75px;top:652px;width:926px;height:2px;background:var(--rule)}
.welcome{left:49px;top:686px;width:451px;height:252px;background:rgba(200,202,198,.6);border-radius:8px;padding:14px 37px 0 36px}
.welcome h2{font-weight:400;font-size:25px;color:var(--welcome);margin-bottom:6px}
.welcome p{font-family:"Noto Sans",Verdana,sans-serif;font-size:12.5px;line-height:17.4px;text-align:justify;hyphens:auto;-webkit-hyphens:auto;color:#333}
.projects-title{left:527px;top:674px;font-size:22px;font-weight:400;color:#333}
.thumb{height:110px;border:1px solid #444}
.thumb.blue{background:linear-gradient(150deg,#2f8a80 0%,#2f62b4 45%,#5e9fa0 80%,#b9c7a0 100%)}
.thumb.gold{background:linear-gradient(150deg,#6b6136 0%,#9c8f54 35%,#244a8a 60%,#b8b27a 100%)}
.footer{left:0;top:963px;width:1077px;height:237px;background:linear-gradient(180deg,#3a3a3a,var(--footer))}
.links{font-size:12.5px;line-height:15.9px;color:#fff;list-style:none}
.contact{left:453px;top:996px}
.queries{left:727px;top:968px;color:#fff;font-size:13px}
.field{left:728px;width:258px;background:var(--field);color:#eee;font-size:13px;padding:6px 11px}
.submit{left:912px;top:1167px;width:73px;height:26px;background:var(--submit);color:#fff;font-size:13px;display:flex;align-items:center;justify-content:center}
.copyright{left:50px;top:1163px;color:#fff;font-size:12.5px}
</style>
</head>
<body>
<div class="abs topbar"></div>
<div class="abs page"></div>

<header>
  <div class="abs brand"><div class="brand-dot"></div><div class="brand-name">Tidewater<br>Habitats</div></div>
  <div class="abs search"><span>Search</span>
    <svg width="30" height="26" viewBox="0 0 30 26"><circle cx="11" cy="11" r="8" fill="none" stroke="#2bb6da" stroke-width="3"/><line x1="17" y1="17" x2="27" y2="24" stroke="#2bb6da" stroke-width="4" stroke-linecap="round"/></svg>
  </div>
  <div class="abs follow">Follow Us on :</div>
  <div class="abs social" style="left:950px"></div>
  <div class="abs social" style="left:976px"></div>
  <div class="abs social" style="left:1002px;background:#2c5aa0"></div>

  <nav class="abs nav">
    <a class="nav-item"><div class="tile" style="background:var(--teal-1)"><svg width="46" height="46" viewBox="0 0 46 46"><path d="M6 6h34v27H22l-8 8v-8H6z" fill="none" stroke="#fff" stroke-width="3.5" stroke-linejoin="round"/><circle cx="23" cy="16" r="4.5" fill="#fff"/><path d="M14 29c1-6 17-6 18 0z" fill="#fff"/></svg></div><span class="nav-label" style="color:#1d6a62">Button 2</span></a>
    <a class="nav-item"><div class="tile" style="background:var(--teal-2)"><svg width="46" height="46" viewBox="0 0 46 46"><path d="M5 22L23 6l18 16M10 18v22h26V18" fill="none" stroke="#fff" stroke-width="3.5" stroke-linejoin="round"/><rect x="18" y="22" width="10" height="10" fill="none" stroke="#fff" stroke-width="3"/></svg></div><span class="nav-label" style="color:#4a9e96">Button 3</span></a>
    <a class="nav-item"><div class="tile" style="background:var(--teal-3)"><svg width="46" height="46" viewBox="0 0 46 46"><path d="M6 6h34v27H22l-8 8v-8H6z" fill="none" stroke="#fff" stroke-width="3.5" stroke-linejoin="round"/><circle cx="23" cy="16" r="4.5" fill="#fff"/><path d="M14 29c1-6 17-6 18 0z" fill="#fff"/></svg></div><span class="nav-label" style="color:#1d6a62">Button 4</span></a>
    <a class="nav-item"><div class="tile" style="background:var(--teal-4)"><svg width="46" height="46" viewBox="0 0 46 46"><path d="M22 6c-10 0-17 6-17 13 0 4 2 7 5 9l-2 8 8-5" fill="none" stroke="#fff" stroke-width="3.5" stroke-linejoin="round"/><rect x="15" y="15" width="26" height="20" rx="6" fill="none" stroke="#fff" stroke-width="3.5"/><path d="M21 22h14M21 27h14" stroke="#fff" stroke-width="3"/></svg></div><span class="nav-label" style="color:#10403c">Button 5</span></a>
    <a class="nav-item"><div class="tile" style="background:var(--olive-1)"><svg width="46" height="46" viewBox="0 0 46 46"><path d="M5 22L23 6l18 16M10 18v22h26V18" fill="none" stroke="#fff" stroke-width="3.5" stroke-linejoin="round"/><rect x="18" y="22" width="10" height="10" fill="none" stroke="#fff" stroke-width="3"/></svg></div><span class="nav-label" style="color:#6f8a1f">Button 6</span></a>
    <a class="nav-item"><div class="tile" style="background:var(--olive-2)"><svg width="46" height="46" viewBox="0 0 46 46"><path d="M6 6h34v27H22l-8 8v-8H6z" fill="none" stroke="#fff" stroke-width="3.5" stroke-linejoin="round"/><circle cx="23" cy="16" r="4.5" fill="#fff"/><path d="M14 29c1-6 17-6 18 0z" fill="#fff"/></svg></div><span class="nav-label" style="color:#5b731a">Button 7</span></a>
    <a class="nav-item"><div class="tile" style="background:var(--olive-3)"><svg width="46" height="46" viewBox="0 0 46 46"><path d="M22 6c-10 0-17 6-17 13 0 4 2 7 5 9l-2 8 8-5" fill="none" stroke="#fff" stroke-width="3.5" stroke-linejoin="round"/><rect x="15" y="15" width="26" height="20" rx="6" fill="none" stroke="#fff" stroke-width="3.5"/><path d="M21 22h14M21 27h14" stroke="#fff" stroke-width="3"/></svg></div><span class="nav-label" style="color:#3c4c12">Button 8</span></a>
    <a class="nav-item"><div class="tile" style="background:var(--olive-4)"><svg width="46" height="46" viewBox="0 0 46 46"><path d="M6 6h34v27H22l-8 8v-8H6z" fill="none" stroke="#fff" stroke-width="3.5" stroke-linejoin="round"/><circle cx="23" cy="16" r="4.5" fill="#fff"/><path d="M14 29c1-6 17-6 18 0z" fill="#fff"/></svg></div><span class="nav-label" style="color:#4d5f14">Button 9</span></a>
  </nav>
</header>

<main>
  <div class="abs hero-shadow"></div>
  <section class="abs hero" role="img" aria-label="Photo of a blue bird of paradise hanging from a branch">
    <div class="hero-caption">" Encompassing Culture. Custom &amp; Science "</div>
  </section>
  <section class="abs slides">
    <div class="slide active"><svg width="20" height="26" viewBox="0 0 20 26"><path d="M12 3L3 13l9 10M18 3L9 13l9 10" fill="none" stroke="var(--chevron)" stroke-width="2"/></svg><div><h3>Slider 1</h3><p>The atmosphere of the Earth serves as a key factor in sustaining the planetary ecosystem.</p></div></div>
    <div class="slide"><svg width="20" height="26" viewBox="0 0 20 26"><path d="M12 3L3 13l9 10M18 3L9 13l9 10" fill="none" stroke="var(--chevron)" stroke-width="2"/></svg><div><h3>Slider 2</h3><p>The atmosphere of the Earth serves as a key factor in sustaining the planetary ecosystem.</p></div></div>
    <div class="slide"><svg width="20" height="26" viewBox="0 0 20 26"><path d="M12 3L3 13l9 10M18 3L9 13l9 10" fill="none" stroke="var(--chevron)" stroke-width="2"/></svg><div><h3>Slider 3</h3><p>The atmosphere of the Earth serves as a key factor in sustaining the planetary ecosystem.</p></div></div>
    <div class="slide"><svg width="20" height="26" viewBox="0 0 20 26"><path d="M12 3L3 13l9 10M18 3L9 13l9 10" fill="none" stroke="var(--chevron)" stroke-width="2"/></svg><div><h3>Slider 4</h3><p>The atmosphere of the Earth serves as a key factor in sustaining the planetary ecosystem.</p></div></div>
  </section>

  <div class="abs rule"></div>

  <section class="abs welcome">
    <h2>Welcome!</h2>
    <p>The potential dangers of global warming are being increasingly studied by a wide global consortium of scientists. These scientists are increasingly concerned about the potential long-term effects of global warming on our natural environment and on the planet. Of particular concern is how climate change and global warming caused by anthropogenic, or human-made releases of greenhouse gases, most notably carbon dioxide, can act interactively, and have adverse effects upon the planet, its natural environment and humans' existence.</p>
  </section>

  <h2 class="abs projects-title">Our Projects</h2>
  <div class="abs thumb blue" style="left:533px;top:712px;width:163px" role="img" aria-label="Project photo: blue bird of paradise"></div>
  <div class="abs thumb gold" style="left:701px;top:712px;width:151px" role="img" aria-label="Project photo: bird of paradise on a branch"></div>
  <div class="abs thumb blue" style="left:857px;top:712px;width:164px" role="img" aria-label="Project photo: blue bird of paradise"></div>
  <div class="abs thumb blue" style="left:533px;top:827px;width:163px" role="img" aria-label="Project photo: blue bird of paradise"></div>
  <div class="abs thumb gold" style="left:701px;top:827px;width:151px" role="img" aria-label="Project photo: bird of paradise on a branch"></div>
  <div class="abs thumb blue" style="left:857px;top:827px;width:164px" role="img" aria-label="Project photo: blue bird of paradise"></div>
</main>

<footer>
  <div class="abs footer"></div>
  <ul class="abs links" style="left:61px;top:994px"><li>Button 1</li><li>Button 2</li><li>Button 3</li><li>Button 4</li><li>Button 5</li><li>Button 6</li><li>Button 7</li><li>Button 8</li></ul>
  <ul class="abs links" style="left:223px;top:994px"><li>Button 1</li><li>Button 2</li><li>Button 3</li><li>Button 4</li><li>Button 5</li><li>Button 6</li><li>Button 7</li><li>Button 8</li></ul>
  <ul class="abs links contact"><li>Contact Info</li><li>Addres Details</li><li>Telephone No.</li><li>Fax No.</li><li>Email id:</li></ul>
  <div class="abs queries">Queries / Comments</div>
  <div class="abs field" style="top:993px;height:30px">Name</div>
  <div class="abs field" style="top:1029px;height:31px">Contact No.</div>
  <div class="abs field" style="top:1066px;height:31px">Email id</div>
  <div class="abs field" style="top:1103px;height:57px">Comments</div>
  <div class="abs submit">Submit</div>
  <div class="abs copyright">Copyright All right reserved</div>
</footer>
</body>
</html>
```